Velmora Sports Foundation website

Velmora sports foundation is a charity organisation that assists young athletes and clubs with the financial assistance they need to progress in their sporting career.

The organisation also establishes mentoring programs to community clubs and individuals.
We envision a home page with a horizontal navigation
Contact Us
Donate: A link to a secure payment system
Meet the team: A list of names and images of the board
Lastly the link to donate should be featured prominently and several times along with cues that lead people to find out more
We prefer limited scrolling and would like to see a clean yet modern design

I am unsure if it needs to be coded or not

Target Market(s)

Potential donors, applications for funds, potential affiliates

Industry/Entity Type

Charity

Coding

Coded - Design and coding required

Number of Pages Required

5+ page

Font styles to use
Sans Serif

Colors
3176b5
ec1f27
34a7d7

Requirements
Must have
• emotionally engaging and informative
• motion enabled pictures
• links to donate
• Music
• Enable video uploads
• Large horizontal pictures of young sports players prominently soccer at this stage
• Social media presence
Nice to have
• Live chat
Should not have
• Images that depict poverty

```html
<!DOCTYPE html>
<html lang="en">
<head>
<meta charset="utf-8">
<title>Velmora Sports Foundation</title>
<link rel="stylesheet" href="https://fonts.googleapis.com/css2?family=Open+Sans:wght@400;600;700&family=Montserrat:wght@500;600&display=swap">
<style>
:root{
  --blue:#0b4ea2;
  --red:#ec1f27;
  --text:#555;
  --dark:#1d1d1d;
  --service-bg:#f3f3f4;
  --footer-bg:#f1f1f1;
  --green:#5aa51b;
  --line:#dcdcdc;
}
*{margin:0;padding:0;box-sizing:border-box}
html,body{width:1200px;height:2446px;overflow:hidden;background:#fff}
body{font-family:"Open Sans",Arial,sans-serif;color:var(--text);position:relative}
a{text-decoration:none;color:inherit}

/* header */
.site-header{position:absolute;left:0;top:0;width:1200px;height:134px;background:#fff}
.brand{position:absolute;left:73px;top:40px;display:flex;align-items:center;gap:12px;color:var(--blue);font-weight:700;font-size:19px;line-height:1.1;width:200px}
.brand-dot{width:44px;height:44px;border-radius:50%;background:var(--red);flex:none}
.main-nav a{position:absolute;top:58px;font-size:15px;color:var(--dark);letter-spacing:.3px}
.nav-donate{position:absolute;left:709px;top:46px;width:139px;height:42px;background:var(--red);color:#fff;border-radius:2px;font-size:15px;display:flex;align-items:center;justify-content:center;gap:10px}
.live-chat{position:absolute;left:1001px;top:44px;width:122px;height:42px;background:linear-gradient(#7cc52c,#3f8c10);border:1px solid #367b0c;border-radius:3px;color:#1f1f1f;font-family:"Montserrat",sans-serif;font-weight:600;font-size:16px;display:flex;align-items:center;justify-content:center;gap:8px}
.live-chat::after{content:"";position:absolute;left:76px;bottom:-12px;border-left:10px solid transparent;border-top:12px solid #3f8c10}

/* hero */
.hero{position:absolute;left:0;top:134px;width:1200px;height:521px;background:radial-gradient(ellipse at 35% 45%,#6c8a45 0%,#3e5a24 45%,#22351a 100%)}
.hero-title{position:absolute;right:75px;top:96px;text-align:right;color:#fff;font-weight:700;font-size:60px;line-height:66px;font-variant:small-caps;letter-spacing:1px}
.hero-text{position:absolute;right:75px;top:251px;text-align:right;color:#fff;font-size:17px;line-height:27px;font-weight:600}
.hero-btn{position:absolute;left:934px;top:329px;width:189px;height:49px;background:var(--red);color:#fff;font-size:16px;display:flex;align-items:center;justify-content:center;gap:10px}
.hero-dots{position:absolute;left:560px;top:480px;display:flex;gap:10px}
.hero-dots span{width:13px;height:13px;border-radius:50%;background:#fff}
.hero-dots span.active{background:transparent;border:2px solid #fff}

/* welcome */
.section-title{font-weight:700;font-size:28px;color:var(--blue);letter-spacing:.5px}
.welcome{position:absolute;left:75px;top:718px;width:571px}
.welcome p{font-size:13px;line-height:27.5px;text-align:justify;margin-top:0}
.welcome .p1{margin-top:48px}
.welcome .p2{margin-top:28px}
.btn-blue{display:flex;align-items:center;justify-content:center;background:var(--blue);color:#fff;font-size:13px;font-weight:600;border-radius:2px}
.welcome .btn-blue{width:124px;height:36px;margin-top:28px}
.video{position:absolute;left:706px;top:718px}
.video-frame{position:absolute;left:-2px;top:79px;width:422px;height:277px;background:linear-gradient(135deg,#2c2a33 0%,#6b5a3a 45%,#5c1f2a 75%,#2a1a22 100%)}
.play{position:absolute;left:181px;top:108px}

/* services */
.services{position:absolute;left:0;top:1167px;width:1200px;height:468px;background:var(--service-bg)}
.services .section-title{position:absolute;width:1200px;text-align:center;top:72px;color:var(--red)}
.service{position:absolute;top:142px;width:230px}
.service-icon{width:72px;height:72px;border:2px solid var(--red);border-radius:50%;display:flex;align-items:center;justify-content:center}
.service h3{font-family:"Montserrat",sans-serif;font-weight:600;font-size:16px;color:var(--dark);line-height:21px;margin-top:27px}
.service p{font-size:13px;line-height:22px;text-align:justify;margin-top:16px}
.learn{display:flex;align-items:center;gap:7px;color:var(--red);font-size:13px;margin-top:17px}

/* blog */
.blog .section-title{position:absolute;width:1200px;text-align:center;top:1710px}
.card{position:absolute;top:1785px;width:243px;height:443px;border:1px solid var(--line);background:#fff;text-align:center}
.card-img{height:217px}
.card time{display:block;color:var(--blue);font-weight:700;font-size:14px;margin-top:29px}
.card h3{color:var(--dark);font-weight:700;font-size:16px;margin-top:6px}
.card p{font-size:13px;line-height:20px;margin:13px 18px 0}
.card .btn-blue{width:117px;height:34px;margin:26px auto 0}

/* footer */
.site-footer{position:absolute;left:0;top:2302px;width:1200px;height:144px;background:var(--footer-bg)}
.footer-links{position:absolute;left:75px;top:60px;font-size:13px;font-weight:600;color:var(--dark);display:flex;gap:14px}
.copyright{position:absolute;left:75px;top:88px;font-size:13px;font-weight:600;color:var(--dark)}
.touch{position:absolute;left:895px;top:74px;font-size:13px;font-weight:600;color:var(--dark)}
.social{position:absolute;top:63px;width:36px;height:36px;border:2px solid var(--red);border-radius:50%}
</style>
</head>
<body>

<header class="site-header">
  <a class="brand" href="#"><span class="brand-dot"></span><span>Velmora Sports Foundation</span></a>
  <nav class="main-nav">
    <a href="#" style="left:349px">HOME</a>
    <a href="#" style="left:445px">PROGRAM</a>
    <a href="#" style="left:571px">MEET THE TEAM</a>
    <a href="#" class="nav-donate">
      <svg width="20" height="18" viewBox="0 0 20 18"><path d="M10 17 2 9a4.5 4.5 0 0 1 8-5 4.5 4.5 0 0 1 8 5z" fill="#fff"/></svg>DONATE</a>
    <a href="#" style="left:875px">CONTACT US</a>
    <a href="#" class="live-chat">
      <svg width="16" height="18" viewBox="0 0 16 18"><circle cx="8" cy="5" r="4.5" fill="#1f1f1f"/><path d="M0 18a8 7 0 0 1 16 0z" fill="#1f1f1f"/></svg>LIVE CHAT</a>
  </nav>
</header>

<section class="hero">
  <div role="img" aria-label="Soccer ball hitting the goal net on a green pitch" style="position:absolute;inset:0"></div>
  <h1 class="hero-title">Sports<br>Foundation</h1>
  <p class="hero-text">Maecenas dignissim nunc in nibh ullamcorper maximus<br>Mauris id bibendum est, at lobortis maur</p>
  <a href="#" class="hero-btn">
    <svg width="14" height="14" viewBox="0 0 14 14"><circle cx="7" cy="7" r="7" fill="#fff"/><path d="M5.5 4 8.5 7 5.5 10" stroke="#ec1f27" stroke-width="2" fill="none"/></svg>LEARN MORE</a>
  <div class="hero-dots"><span class="active"></span><span></span><span></span><span></span></div>
</section>

<section class="welcome">
  <h2 class="section-title">WELCOME</h2>
  <p class="p1">Phasellus mattis imperdiet odio ac faucibus. Nunc tristique sem at ipsum feugiat auctor. Fusce suscipit dignissim ornare. Maecenas dignissim nunc in nibh ullamcorper maximus.</p>
  <p class="p2">Mauris id bibendum est, at lobortis mauris. Praesent aliquet eros nisi, ac aliquet ex ornare euPhasellus mattis imperdiet odio ac faucibus. Nunc tristique sem at ipsum feugiat auctor. Fusce suscipit dignissim ornare. Maecenas dignissim. Nunc tristique sem at ipsum feugiat auctor. Fusce suscipit dignissim ornare. Maecenas dignissim.</p>
  <a href="#" class="btn-blue">READ MORE</a>
</section>

<section class="video">
  <h2 class="section-title">WATCH VIDEO</h2>
  <div class="video-frame" role="img" aria-label="Video still of a climber in a red cape on a mountain cliff">
    <svg class="play" width="60" height="60" viewBox="0 0 60 60"><circle cx="30" cy="30" r="26" fill="none" stroke="#fff" stroke-width="5"/><path d="M23 17 43 30 23 43z" fill="#fff"/></svg>
  </div>
</section>

<section class="services">
  <h2 class="section-title">OUR SERVICES</h2>
  <div class="service" style="left:75px">
    <div class="service-icon"><svg width="24" height="22" viewBox="0 0 24 22"><path d="M3 1v21" stroke="#ec1f27" stroke-width="2.5"/><path d="M4 2h17l-4 5 4 5H4z" fill="#ec1f27"/></svg></div>
    <h3>ALIQUAM<br>AT NIBH SED</h3>
    <p>Maecenas dignissim. Nunc tristique sem at ipsum feugiat auctor. Fusce suscipit dignissim ornare.</p>
    <a href="#" class="learn"><svg width="11" height="11" viewBox="0 0 14 14"><circle cx="7" cy="7" r="7" fill="#ec1f27"/><path d="M5.5 4 8.5 7 5.5 10" stroke="#fff" stroke-width="2" fill="none"/></svg>LEARN MORE</a>
  </div>
  <div class="service" style="left:350px">
    <div class="service-icon"><svg width="26" height="26" viewBox="0 0 26 26"><circle cx="13" cy="13" r="12" fill="#ec1f27"/><circle cx="13" cy="13" r="3.5" fill="#fff"/><circle cx="6" cy="9" r="2.3" fill="#fff"/><circle cx="20" cy="9" r="2.3" fill="#fff"/><circle cx="8.5" cy="19.5" r="2.3" fill="#fff"/><circle cx="17.5" cy="19.5" r="2.3" fill="#fff"/></svg></div>
    <h3>SUSPENDIS<br>NON QUAM A FEL</h3>
    <p>Maecenas dignissim. Nunc tristique sem at ipsum feugiat auctor. Fusce suscipit dignissim ornare.</p>
    <a href="#" class="learn"><svg width="11" height="11" viewBox="0 0 14 14"><circle cx="7" cy="7" r="7" fill="#ec1f27"/><path d="M5.5 4 8.5 7 5.5 10" stroke="#fff" stroke-width="2" fill="none"/></svg>LEARN MORE</a>
  </div>
  <div class="service" style="left:621px">
    <div class="service-icon"><svg width="20" height="26" viewBox="0 0 20 26"><path d="M10 26S1 15 1 9.5a9 9 0 0 1 18 0C19 15 10 26 10 26z" fill="#ec1f27"/><circle cx="10" cy="9.5" r="3.5" fill="#fff"/></svg></div>
    <h3>PRAESENT<br>VARIUS MOLLIS</h3>
    <p>Maecenas dignissim. Nunc tristique sem at ipsum feugiat auctor. Fusce suscipit dignissim ornare.</p>
    <a href="#" class="learn"><svg width="11" height="11" viewBox="0 0 14 14"><circle cx="7" cy="7" r="7" fill="#ec1f27"/><path d="M5.5 4 8.5 7 5.5 10" stroke="#fff" stroke-width="2" fill="none"/></svg>LEARN MORE</a>
  </div>
  <div class="service" style="left:896px">
    <div class="service-icon"><svg width="22" height="24" viewBox="0 0 22 24"><circle cx="11" cy="7" r="6" fill="#ec1f27"/><path d="M0 24a11 10 0 0 1 22 0z" fill="#ec1f27"/></svg></div>
    <h3>NIBH GRA<br>VIDA MATTIS</h3>
    <p>Maecenas dignissim. Nunc tristique sem at ipsum feugiat auctor. Fusce suscipit dignissim ornare.</p>
    <a href="#" class="learn"><svg width="11" height="11" viewBox="0 0 14 14"><circle cx="7" cy="7" r="7" fill="#ec1f27"/><path d="M5.5 4 8.5 7 5.5 10" stroke="#fff" stroke-width="2" fill="none"/></svg>LEARN MORE</a>
  </div>
</section>

<section class="blog">
  <h2 class="section-title">FROM THE BLOG</h2>
  <article class="card" style="left:73px">
    <div class="card-img" role="img" aria-label="Young soccer player celebrating on a grass field at sunset" style="background:linear-gradient(180deg,#a8924f 0%,#6d7a3b 55%,#3e6b1f 100%)"></div>
    <time>OCT 31, 2016</time><h3>FUSCE SUSCIPIT DIGN</h3>
    <p>Mauris id bibendum est, at lobort mauris. Praesent aliquet eros nis ac aliquet ex ornare.</p>
    <a href="#" class="btn-blue">READ MORE</a>
  </article>
  <article class="card" style="left:344px">
    <div class="card-img" role="img" aria-label="Climber's hands gripping a rock ledge before snowy mountains" style="background:linear-gradient(180deg,#6f7f95 0%,#8a7a66 55%,#7a6048 100%)"></div>
    <time>OCT 31, 2016</time><h3>FUSCE SUSCIPIT DIGN</h3>
    <p>Mauris id bibendum est, at lobort mauris. Praesent aliquet eros nis ac aliquet ex ornare.</p>
    <a href="#" class="btn-blue">READ MORE</a>
  </article>
  <article class="card" style="left:614px">
    <div class="card-img" role="img" aria-label="Golfer swinging a driver under a blue sky" style="background:linear-gradient(180deg,#6fa3d8 0%,#a9c5e0 55%,#c9b99c 100%)"></div>
    <time>OCT 31, 2016</time><h3>FUSCE SUSCIPIT DIGN</h3>
    <p>Mauris id bibendum est, at lobort mauris. Praesent aliquet eros nis ac aliquet ex ornare.</p>
    <a href="#" class="btn-blue">READ MORE</a>
  </article>
  <article class="card" style="left:885px">
    <div class="card-img" role="img" aria-label="Soccer player kicking a ball against a fiery orange sky" style="background:radial-gradient(ellipse at 50% 40%,#e0701f 0%,#a8341a 55%,#3a1a12 100%)"></div>
    <time>OCT 31, 2016</time><h3>FUSCE SUSCIPIT DIGN</h3>
    <p>Mauris id bibendum est, at lobort mauris. Praesent aliquet eros nis ac aliquet ex ornare.</p>
    <a href="#" class="btn-blue">READ MORE</a>
  </article>
</section>

<footer class="site-footer">
  <nav class="footer-links">
    <a href="#">HOME</a><span>\</span><a href="#">BIO'S</a><span>\</span><a href="#">VIDEO'S</a><span>\</span><a href="#">BLOG</a><span>\</span><a href="#">PRICING</a><span>\</span><a href="#">CONTACT US</a>
  </nav>
  <p class="copyright">COPYRIGHT 2016, ALL RIGHT RESERVED.</p>
  <span class="touch">GET IN TOUCH</span>
  <a href="#" class="social" style="left:1002px" aria-label="Social profile"></a>
  <a href="#" class="social" style="left:1046px" aria-label="Social profile"></a>
  <a href="#" class="social" style="left:1090px" aria-label="Social profile"></a>
</footer>

</body>
</html>
```